Brightfern Care Alliance Flirvo Ads

We want an ad created for the gay dating app flirvo. The size is 300x250. We want the ad to be sexy, with a shirtless man. We are advertising our free HIV and PrEP services. We are open to slogans about maybe "Bringing HIV and PrEP To You"
"Free PrEP and HIV Management"
Open to ideas.

We also offer through the Cedarline Relief Fund
Copay Assistance, Insurance Premium Assistance, Free Medical Services, etc
Our website is bfcanj.org

I do want the ad to have a Book Now Button

Gay sexually active males

```html
<!DOCTYPE html>
<html lang="en">
<head>
<meta charset="utf-8">
<title>Brightfern Care Alliance – Flirvo Ad</title>
<link rel="stylesheet" href="https://fonts.googleapis.com/css2?family=Poppins:wght@400;600;700&display=swap">
<style>
  :root {
    --page-bg: #d9d9d9;
    --navy-deep: #0b0f4a;
    --navy-mid: #17237a;
    --white: #ffffff;
    --ink: #121212;
    --blue: #3d6bff;
    --violet: #8b4dff;
    --magenta: #d43cff;
    --pink: #ff4f86;
    --brand-text: #5a3cf0;
  }
  * { margin: 0; padding: 0; box-sizing: border-box; }
  html, body {
    width: 1200px; height: 1040px; overflow: hidden;
    background: var(--page-bg);
    font-family: "Poppins", sans-serif;
  }
  .ad {
    position: absolute; left: 0; top: 24px;
    width: 1200px; height: 992px;
    overflow: hidden;
  }
  .ad-backdrop { position: absolute; inset: 0; }
  .headline {
    position: absolute; left: 54px; top: 42px;
    color: var(--white);
    font-weight: 600; font-size: 94px; line-height: 108px;
    letter-spacing: -0.5px;
  }
  .headline .accent-hiv {
    background: linear-gradient(90deg, var(--blue), var(--magenta));
    -webkit-background-clip: text; background-clip: text; color: transparent;
  }
  .headline .accent-prep {
    background: linear-gradient(90deg, var(--blue), var(--violet) 50%, var(--pink));
    -webkit-background-clip: text; background-clip: text; color: transparent;
  }
  .benefits {
    position: absolute; left: 54px; top: 400px;
    list-style: none; color: var(--white);
    font-size: 36px; line-height: 48px; font-weight: 400;
  }
  .benefits li {
    display: flex; align-items: flex-start;
    margin-bottom: 21px;
  }
  .benefits .tick { flex: 0 0 32px; width: 32px; height: 32px; margin: 9px 28px 0 4px; }
  .book-button {
    position: absolute; left: 54px; top: 798px;
    width: 458px; height: 80px; border-radius: 40px;
    background: linear-gradient(90deg, var(--blue), var(--violet) 55%, var(--pink));
    color: var(--white);
    font-weight: 700; font-size: 54px; letter-spacing: 0.5px;
    display: flex; align-items: center; justify-content: center;
    text-decoration: none;
  }
  .site-url {
    position: absolute; left: 104px; top: 896px;
    font-size: 48px; color: var(--ink); font-weight: 400;
  }
  .site-url strong { font-weight: 700; }
  .brand-mark {
    position: absolute; left: 748px; top: 808px;
    display: flex; align-items: center; gap: 22px;
  }
  .brand-mark .brand-dot {
    width: 96px; height: 96px; border-radius: 50%;
    background: var(--violet);
  }
  .brand-mark .brand-name {
    font-weight: 600; font-size: 40px; line-height: 46px;
    color: var(--brand-text);
  }
</style>
</head>
<body>
  <section class="ad" aria-label="Brightfern Care Alliance advert for Flirvo">
    <svg class="ad-backdrop" width="1200" height="992" viewBox="0 0 1200 992">
      <defs>
        <linearGradient id="navyFill" x1="0" y1="0" x2="1" y2="1">
          <stop offset="0" stop-color="#0a0e44"/>
          <stop offset="0.5" stop-color="#151f6e"/>
          <stop offset="1" stop-color="#0d1456"/>
        </linearGradient>
        <linearGradient id="ringFill" x1="0" y1="1" x2="1" y2="0">
          <stop offset="0" stop-color="#3d6bff"/>
          <stop offset="0.55" stop-color="#8b4dff"/>
          <stop offset="1" stop-color="#ff4fb0"/>
        </linearGradient>
        <radialGradient id="photoFill" cx="0.45" cy="0.45" r="0.6">
          <stop offset="0" stop-color="#d9a58a"/>
          <stop offset="0.6" stop-color="#b7816a"/>
          <stop offset="1" stop-color="#6e4a3d"/>
        </radialGradient>
      </defs>
      <rect class="navy-field" width="1200" height="992" fill="url(#navyFill)"/>
      <circle class="photo-ring" cx="972" cy="532" r="352" fill="url(#ringFill)"/>
      <circle class="photo-frame" cx="972" cy="532" r="338" fill="#0d1456"/>
      <circle class="hero-photo" cx="972" cy="532" r="326" fill="url(#photoFill)"
              role="img" aria-label="Photo of a shirtless man with arms crossed over his chest"/>
      <path class="white-band" d="M0 840 H600 C660 840 660 776 732 776 H1200 V992 H0 Z" fill="#ffffff"/>
    </svg>

    <h1 class="headline">
      BRINGING <span class="accent-hiv">HIV</span><br>
      AND <span class="accent-prep">PREP</span><br>
      TO YOU
    </h1>

    <ul class="benefits">
      <li><svg class="tick" viewBox="0 0 32 32"><circle cx="16" cy="16" r="13.5" fill="none" stroke="#ffffff" stroke-width="3"/><path d="M9 16.5 L14 21.5 L25 8" fill="none" stroke="#c04dff" stroke-width="4" stroke-linecap="round" stroke-linejoin="round"/></svg><span>Cedarline Relief Fund</span></li>
      <li><svg class="tick" viewBox="0 0 32 32"><circle cx="16" cy="16" r="13.5" fill="none" stroke="#ffffff" stroke-width="3"/><path d="M9 16.5 L14 21.5 L25 8" fill="none" stroke="#c04dff" stroke-width="4" stroke-linecap="round" stroke-linejoin="round"/></svg><span>Copay Assistance,</span></li>
      <li><svg class="tick" viewBox="0 0 32 32"><circle cx="16" cy="16" r="13.5" fill="none" stroke="#ffffff" stroke-width="3"/><path d="M9 16.5 L14 21.5 L25 8" fill="none" stroke="#c04dff" stroke-width="4" stroke-linecap="round" stroke-linejoin="round"/></svg><span>Insurance Premium<br>Assistance,</span></li>
      <li><svg class="tick" viewBox="0 0 32 32"><circle cx="16" cy="16" r="13.5" fill="none" stroke="#ffffff" stroke-width="3"/><path d="M9 16.5 L14 21.5 L25 8" fill="none" stroke="#c04dff" stroke-width="4" stroke-linecap="round" stroke-linejoin="round"/></svg><span>Free Medical Services,</span></li>
    </ul>

    <a class="book-button" href="#">BOOK NOW</a>
    <p class="site-url">www.<strong>bfcanj</strong>.org</p>

    <div class="brand-mark">
      <span class="brand-dot"></span>
      <span class="brand-name">Brightfern<br>Care Alliance</span>
    </div>
  </section>
</body>
</html>
```